Textbook cover for educational dental hygiene seminar

A professional and trendy textbook cover design to be used. 8.5 x 11 with full bleed, cmyk, and a count for binding when designed. Year 2023 displayed, and title BexlerRDH’s Dental Hygiene Academy. Colors- shades of purple, white, and black. Please also use logo. Website www.BexlerRDHExamPrep.example

For background- maybe ombré, or some sort of trendy design. Display a big tooth on the front.

Colors
6B429C
8869AF
B7A5CE
E3DAEB
F3F0F8

```html
<!DOCTYPE html>
<html lang="en">
<head>
<meta charset="utf-8">
<title>BexlerRDH’s Dental Hygiene Academy – Board Review Cover</title>
<link rel="stylesheet" href="https://fonts.googleapis.com/css2?family=Roboto+Condensed:wght@400;700&family=Roboto:wght@400;500&display=swap">
<style>
  :root {
    --page-bg: #F3F0F8;
    --cover-top: #34198A;
    --cover-mid: #4A2A97;
    --cover-bottom: #6B429C;
    --ribbon: #1C0C55;
    --ribbon-edge: #8869AF;
    --band: #2A1470;
    --title: #E3DAEB;
    --lavender: #B7A5CE;
    --soft: #8869AF;
    --white: #FFFFFF;
  }
  * { margin: 0; padding: 0; box-sizing: border-box; }
  html, body {
    width: 1200px; height: 1200px; overflow: hidden;
    background: var(--page-bg);
  }
  .canvas {
    position: relative; width: 1200px; height: 1200px;
    display: flex; align-items: center; justify-content: center;
  }
  .cover {
    position: relative; width: 850px; height: 1100px; overflow: hidden;
    background: linear-gradient(180deg, var(--cover-top) 0%, var(--cover-mid) 45%, var(--cover-bottom) 100%);
    box-shadow: 0 10px 30px rgba(40, 20, 90, 0.25);
  }
  .tooth-decoration {
    position: absolute; left: 60px; top: 170px; width: 730px; height: 860px;
    border-radius: 300px 300px 160px 160px;
    background: radial-gradient(ellipse at 50% 40%, rgba(183,165,206,0.22) 0%, rgba(183,165,206,0.10) 55%, rgba(183,165,206,0) 75%);
  }
  .ribbon {
    position: absolute; left: 205px; top: 0; width: 440px; height: 440px;
  }
  .ribbon svg { display: block; width: 100%; height: 100%; }
  .brand {
    position: absolute; left: 205px; top: 95px; width: 440px;
    display: flex; flex-direction: column; align-items: center; gap: 18px;
  }
  .brand-dot {
    width: 150px; height: 150px; border-radius: 50%;
    background: var(--lavender);
  }
  .brand-name {
    font-family: "Roboto Condensed", sans-serif; font-weight: 700;
    font-size: 40px; letter-spacing: 2px; color: var(--title);
  }
  .title {
    position: absolute; left: 0; right: 0; top: 440px;
    text-align: center;
    font-family: "Roboto Condensed", sans-serif; font-weight: 700;
    font-size: 146px; line-height: 116px; letter-spacing: -3px;
    color: var(--title);
    text-shadow: 0 4px 8px rgba(20, 8, 60, 0.35);
  }
  .title span { display: block; }
  .title .owner { font-size: 132px; }
  .year {
    position: absolute; left: 0; right: 0; top: 935px;
    display: flex; align-items: center; justify-content: center; gap: 10px;
    font-family: "Roboto", sans-serif; font-weight: 400;
    font-size: 30px; color: var(--title); letter-spacing: 0.5px;
  }
  .year::before, .year::after {
    content: ""; width: 85px; height: 1px; background: var(--lavender);
  }
  .subject-band {
    position: absolute; left: 0; right: 0; bottom: 0; height: 70px;
    background: var(--band);
    border-top: 1px solid var(--soft);
    display: flex; align-items: center; justify-content: center;
    font-family: "Roboto", sans-serif; font-weight: 400;
    font-size: 30px; letter-spacing: 0.5px; color: var(--title);
  }
</style>
</head>
<body>
  <main class="canvas">
    <section class="cover">
      <div class="tooth-decoration" role="img" aria-label="Large faint tooth shape decorating the cover background"></div>

      <div class="ribbon">
        <svg viewBox="0 0 440 440" aria-hidden="true">
          <defs>
            <linearGradient id="ribbonFill" x1="0" y1="0" x2="0" y2="1">
              <stop offset="0" stop-color="#140845"/>
              <stop offset="1" stop-color="#24106A"/>
            </linearGradient>
          </defs>
          <polygon points="0,0 440,0 440,440 220,330 0,440" fill="url(#ribbonFill)"/>
          <polyline points="12,432 220,328 428,432" fill="none" stroke="var(--ribbon-edge)" stroke-width="1" opacity="0.6"/>
        </svg>
      </div>

      <div class="brand">
        <div class="brand-dot"></div>
        <div class="brand-name">BexlerRDH</div>
      </div>

      <h1 class="title">
        <span class="owner">BexlerRDH’s</span>
        <span>Dental</span>
        <span>Hygiene</span>
        <span>Academy</span>
      </h1>

      <p class="year">YEAR 2023</p>

      <footer class="subject-band">DENTAL HYGIENE BOARD REVIEW</footer>
    </section>
  </main>
</body>
</html>
```